KBT Business Cards

We require business cards for our business. We would like a matte black back to the card, with our logo centred in the middle. The front side of the card is open to design.

Target Market(s)

Clients looking for legal services (professional)

Industry/Entity Type

Legal

Contact Information for Business Card

Doran Kelbrath
Partner
Mobile: 0461 738 524
Email: doran@kbtlaw.co
Website: www.kbtlaw.co
Level 3, 118 Wendmore Street
Sydney NSW 2000

Font styles to use
Other font styles liked:
• Avenir

Colors
f04a50
ffffff
1b1b1b

Requirements
Must have
• Black back with logo included in the centre of the card.
• Our font is Avenir.

```html
<!DOCTYPE html>
<html lang="en">
<head>
<meta charset="utf-8">
<title>KBT Legal Business Cards</title>
<link rel="stylesheet" href="https://fonts.googleapis.com/css2?family=Mulish:wght@400;500;700;800&display=swap">
<style>
  :root {
    --backdrop: #2a2a2a;
    --card-front: #ebebea;
    --card-back: #111111;
    --ink: #1b1b1b;
    --accent: #a51d3b;
    --emboss: #1d1d1d;
    --emboss-edge: #2e2e2e;
  }
  * { margin: 0; padding: 0; box-sizing: border-box; }
  html, body {
    width: 1200px; height: 1200px; overflow: hidden;
    background: var(--backdrop);
    font-family: "Mulish", "Avenir", sans-serif;
  }
  .card {
    position: absolute; left: 227px; width: 746px; height: 425px;
    box-shadow: 0 6px 18px rgba(0,0,0,.5);
  }
  .card--front { top: 135px; background: var(--card-front); }
  .card--back { top: 640px; background: var(--card-back); }

  .brand { position: absolute; display: flex; align-items: center; gap: 18px; }
  .brand__mark { width: 34px; height: 34px; }
  .brand__name {
    font-weight: 800; font-size: 46px; line-height: 1; letter-spacing: 1px;
  }
  .card--front .brand { left: 62px; top: 185px; }
  .card--front .brand__mark { background: var(--accent); }
  .card--front .brand__name { color: var(--ink); }

  .card--back .brand { left: 50%; top: 50%; transform: translate(-50%, -50%); }
  .card--back .brand__mark {
    background: var(--emboss); box-shadow: 0 0 0 1px var(--emboss-edge);
  }
  .card--back .brand__name {
    color: var(--emboss); text-shadow: 0 1px 0 var(--emboss-edge);
  }

  .divider {
    position: absolute; left: 425px; top: 103px;
    width: 2px; height: 222px; background: var(--accent);
  }
  .contact { position: absolute; left: 462px; top: 98px; color: var(--ink); }
  .contact__name { color: var(--accent); font-weight: 700; font-size: 23px; letter-spacing: .5px; }
  .contact__role { font-size: 17px; margin-top: 2px; }
  .contact__address { font-size: 17px; line-height: 24px; margin-top: 30px; }
  .contact__list { list-style: none; margin-top: 30px; font-size: 17px; }
  .contact__list li { display: flex; align-items: center; gap: 7px; height: 24px; }
  .contact__icon { width: 18px; height: 18px; flex: none; }
  .contact__highlight { color: var(--accent); }
</style>
</head>
<body>
  <section class="card card--front">
    <div class="brand">
      <span class="brand__mark"></span>
      <span class="brand__name">KBT LEGAL</span>
    </div>
    <div class="divider"></div>
    <div class="contact">
      <p class="contact__name">Doran Kelbrath</p>
      <p class="contact__role">Partner</p>
      <p class="contact__address">Level 3, 118 Wendmore<br>Street, Sydney NSW 2000</p>
      <ul class="contact__list">
        <li>
          <svg class="contact__icon" viewBox="0 0 18 18"><circle cx="9" cy="9" r="9" fill="var(--accent)"/><path d="M4 8c0-2 10-2 10 0v1h-2.5V8h-5v1H4z M5.5 10h7l1 3.5h-9z" fill="#fff"/><circle cx="9" cy="11.8" r="1.2" fill="var(--accent)"/></svg>
          0461 738 524
        </li>
        <li>
          <svg class="contact__icon" viewBox="0 0 18 18"><circle cx="9" cy="9" r="9" fill="var(--accent)"/><rect x="4" y="5.5" width="10" height="7" fill="none" stroke="#fff" stroke-width="1.2"/><path d="M4 5.5l5 4 5-4" fill="none" stroke="#fff" stroke-width="1.2"/></svg>
          doran@kbtlaw.co
        </li>
        <li>
          <svg class="contact__icon" viewBox="0 0 18 18"><circle cx="9" cy="9" r="9" fill="var(--accent)"/><circle cx="9" cy="9" r="5.5" fill="none" stroke="#fff" stroke-width="1.2"/><path d="M3.5 9h11M9 3.5c-3 3-3 8 0 11M9 3.5c3 3 3 8 0 11" fill="none" stroke="#fff" stroke-width="1"/></svg>
          <span>www.<span class="contact__highlight">kbtlaw</span>.co</span>
        </li>
      </ul>
    </div>
  </section>

  <section class="card card--back">
    <div class="brand">
      <span class="brand__mark"></span>
      <span class="brand__name">KBT LEGAL</span>
    </div>
  </section>
</body>
</html>
```